Design an Invitation for a cool Black and White Party, printable

Hi everyone,

we are making a black and white party and need some invitations. Theme should be the silhouettes of us two (abstract) and then whatever you find cool.

There is some Text too, 4-6 sentences.

Obv. it has to be blaack&white :)

This has to be printable in postcard format.

EDIT: Added pivtures for the silhouettes.. For me it´s a duit, for the lady it´s a dress.. We are going for something like this, but cooler: [url removed, login to view]

EDIT: The text

--Start Text---
Ihr seid eingeladen zum Black & White Grillen!

Am 22. Juli dieses Jahres werfen wir ab 14 Uhr den Grill an und feiern zusammen bis spät in die Nacht. Über euer Erscheinen mit maximal 4 Begleitpersonen freuen wir uns. Für Grillfleisch und Getränke ist gesorgt…

So geht es: Zusagen - wann und mit wem ihr kommt. Herausputzen – in schwarz und weiß. Salate und Getränke eurer Wahl mitbringen – und ab in den Haselkampweg 3!

Es wird einen Fahrer geben, der von ca. 18 Uhr bis 4 Uhr alle nach Hause fährt, die getrunken haben. Schlafplätze sind limitiert – first come, first serve.

----End text----

Edit: Contest now sealed

```html
<!DOCTYPE html>
<html lang="de">
<head>
<meta charset="utf-8">
<title>Black &amp; White Grillen – Einladung</title>
<link rel="stylesheet" href="https://fonts.googleapis.com/css2?family=EB+Garamond:wght@400;500&family=Didact+Gothic&family=Arimo:wght@700&display=swap">
<style>
  :root {
    --ink: #1a1a1a;
    --paper: #ffffff;
    --night: #1e1e1e;
    --silhouette-light: #ffffff;
    --silhouette-shade: #d9d9d9;
  }
  html, body {
    margin: 0;
    padding: 0;
    overflow: hidden;
    background: var(--paper);
  }
  .invitation {
    position: relative;
    width: 1200px;
    height: 900px;
    overflow: hidden;
    background: var(--paper);
    color: var(--ink);
  }
  .backdrop {
    position: absolute;
    inset: 0;
  }
  .panel-light { fill: var(--paper); }
  .panel-dark { fill: var(--night); }
  .dot-dark { fill: var(--ink); }
  .dot-light { fill: var(--paper); }

  .headline-intro,
  .headline-black,
  .headline-amp,
  .headline-white,
  .headline-grill {
    position: absolute;
    margin: 0;
    line-height: 1;
    white-space: nowrap;
    font-weight: 400;
  }
  .headline-intro {
    left: 29px;
    top: 52px;
    font-family: "EB Garamond", serif;
    font-size: 50px;
    font-weight: 500;
    letter-spacing: 0.3px;
  }
  .headline-black {
    left: 278px;
    top: 120px;
    font-family: "Didact Gothic", sans-serif;
    font-size: 112px;
    letter-spacing: -1px;
  }
  .headline-amp {
    left: 490px;
    top: 188px;
    font-family: "EB Garamond", serif;
    font-size: 122px;
    font-weight: 500;
  }
  .headline-white {
    left: 612px;
    top: 130px;
    font-family: "Arimo", sans-serif;
    font-weight: 700;
    font-size: 100px;
    color: var(--paper);
    letter-spacing: -1px;
  }
  .headline-grill {
    left: 808px;
    top: 228px;
    font-family: "EB Garamond", serif;
    font-size: 92px;
    color: var(--paper);
  }

  .details p {
    position: absolute;
    margin: 0;
    font-family: "Didact Gothic", sans-serif;
    font-size: 23px;
    line-height: 29px;
    white-space: nowrap;
  }
  .details .when { left: 16px; top: 316px; }
  .details .how { left: 63px; top: 530px; }
  .details .ride { left: 9px; top: 689px; }

  .couple {
    position: absolute;
    left: 828px;
    top: 320px;
    width: 340px;
    height: 540px;
    border-radius: 150px 150px 30px 30px;
    background: linear-gradient(180deg, var(--silhouette-light) 0%, var(--silhouette-shade) 100%);
  }
</style>
</head>
<body>
  <main class="invitation">
    <svg class="backdrop" width="1200" height="900" viewBox="0 0 1200 900" aria-hidden="true">
      <rect class="panel-light" x="0" y="0" width="591" height="900"/>
      <rect class="panel-dark" x="591" y="0" width="609" height="900"/>
      <circle class="dot-dark" cx="137" cy="229" r="85"/>
      <circle class="dot-dark" cx="32" cy="564" r="25"/>
      <circle class="dot-dark" cx="451" cy="847" r="44"/>
      <circle class="dot-light" cx="1107" cy="97" r="97"/>
      <circle class="dot-light" cx="691" cy="377" r="61"/>
      <circle class="dot-light" cx="744" cy="740" r="85"/>
    </svg>

    <h1 class="headline">
      <span class="headline-intro">Ihr seid eingeladen zum</span>
      <span class="headline-black">Black</span>
      <span class="headline-amp">&amp;</span>
      <span class="headline-white">White</span>
      <span class="headline-grill">Grillen!</span>
    </h1>

    <section class="details">
      <p class="when">Am 22. Juli dieses Jahres werfen wir ab 14<br>Uhr den Grill an und feiern zusammen bis<br>spät in die Nacht. Über euer Erscheinen mit<br>maximal 4<br>Begleitpersonen freuen&nbsp; wir uns. Für<br>Grillfleisch und Getränke ist gesorgt…</p>
      <p class="how">So geht es: Zusagen -&nbsp; wann und mit wem<br>ihr kommt. Herausputzen – in schwarz und<br>weiß. Salate und Getränke eurer Wahl<br>mitbringen – und ab in den<br>Haselkampweg 3!</p>
      <p class="ride">Es wird einen Fahrer geben, der von ca. 18<br>Uhr bis 4 Uhr alle nach Hause fährt, die<br>getrunken haben. Schlafplätze sind<br>limitiert – first come, first serve.</p>
    </section>

    <div class="couple" role="img" aria-label="White silhouette of a couple: a woman in a flared dress and a man in a suit with bow tie"></div>
  </main>
</body>
</html>
```